American cannabis tech company business card design

Pavrel.com is seeking a modern, professional, and brand-aligned business card that represents our company and its core values: Mission, Story, Values, and Impact. As an innovative cannabis company, we want a business card that is not only visually appealing but also serves as a representation of who we are and what we stand for.

Project Scope: Design a double-sided business card that integrates our brand identity and core values. Incorporate our key brand elements, ensuring a sleek and contemporary aesthetic. Visually reflect our core values (Mission, Story, Values, Impact) in a way that is engaging yet professional.

Target Market(s)

Vendors, third parties,

Contact Information for Business Card

Contact details (name, title, email, phone, website, etc.)

Font styles to use
Other font styles liked:
• Caslon, Centra

Colors

Designer to choose colors to be used in the design.

Requirements
Must have
• Pavrel.com logo and branding A creative yet clean way to integrate our core values (Mission, Story, Values, Impact) Modern typography and a well-structured layout
Nice to have
• forest green, grey, white, black
Should not have
• references to marijuana, leafs, plants, or related product

```html
<!DOCTYPE html>
<html lang="en">
<head>
<meta charset="utf-8">
<title>Pavrel.com Business Card</title>
<link rel="stylesheet" href="https://fonts.googleapis.com/css2?family=Libre+Caslon+Text:wght@400;700&family=Montserrat:wght@400;500&display=swap">
<style>
  :root {
    --bg: #2a2a2a;
    --forest: #1c3a1f;
    --forest-deep: #122a15;
    --ink: #1b3a1d;
    --text: #1d1d1d;
    --paper: #ffffff;
  }
  * { margin: 0; padding: 0; box-sizing: border-box; }
  html, body { width: 1200px; height: 1015px; overflow: hidden; }
  body {
    background: var(--bg);
    display: flex;
    flex-direction: column;
    align-items: center;
    justify-content: center;
    gap: 60px;
  }
  .card {
    width: 700px;
    height: 400px;
    position: relative;
    box-shadow: 0 12px 30px rgba(0,0,0,.45);
  }
  .card-back {
    background: var(--forest);
    display: flex;
    align-items: center;
    justify-content: center;
  }
  .card-back .wordmark {
    font-family: "Libre Caslon Text", Georgia, serif;
    font-weight: 700;
    font-size: 120px;
    letter-spacing: 2px;
    color: var(--forest-deep);
  }
  .card-front { background: var(--paper); }
  .card-front .wordmark {
    position: absolute;
    top: 64px;
    right: 48px;
    font-family: "Libre Caslon Text", Georgia, serif;
    font-weight: 700;
    font-size: 76px;
    letter-spacing: 1px;
    color: var(--ink);
  }
  .person {
    position: absolute;
    top: 92px;
    left: 52px;
    font-family: "Libre Caslon Text", Georgia, serif;
    color: var(--ink);
  }
  .person .name { font-size: 22px; font-weight: 700; }
  .person .role { font-size: 12px; font-weight: 700; color: var(--text); margin-top: 2px; }
  .contact {
    position: absolute;
    left: 52px;
    bottom: 48px;
    font-family: "Montserrat", Arial, sans-serif;
    font-size: 15px;
    line-height: 1.3;
    color: var(--text);
  }
  .address { margin-bottom: 22px; }
  .contact-list { list-style: none; margin-left: 40px; }
  .contact-list li { display: flex; align-items: center; gap: 10px; margin-bottom: 4px; }
  .contact-list svg { width: 14px; height: 14px; fill: var(--ink); flex: none; }
</style>
</head>
<body>
  <section class="card card-back" aria-label="Card back">
    <span class="wordmark">PAVREL</span>
  </section>

  <section class="card card-front" aria-label="Card front">
    <div class="person">
      <div class="name">Daniel Harper</div>
      <div class="role">Owner</div>
    </div>
    <span class="wordmark">PAVREL</span>
    <div class="contact">
      <p class="address">418 Linden Ave, Suite 12<br>Dayton, OH 45402</p>
      <ul class="contact-list">
        <li>
          <svg viewBox="0 0 24 24" aria-hidden="true"><path d="M6.6 10.8a15.1 15.1 0 0 0 6.6 6.6l2.2-2.2a1 1 0 0 1 1-.25 11.4 11.4 0 0 0 3.6.57 1 1 0 0 1 1 1V20a1 1 0 0 1-1 1A17 17 0 0 1 3 4a1 1 0 0 1 1-1h3.5a1 1 0 0 1 1 1c0 1.25.2 2.45.57 3.57a1 1 0 0 1-.25 1z"/></svg>
          555-318-0247
        </li>
        <li>
          <svg viewBox="0 0 24 24" aria-hidden="true"><path d="M2 5h20v14H2z M2 5l10 8 10-8" /></svg>
          info@pavrel.com
        </li>
        <li>
          <svg viewBox="0 0 24 24" aria-hidden="true"><circle cx="12" cy="12" r="10"/><path d="M2 12h20M12 2c3 3 3 17 0 20M12 2c-3 3-3 17 0 20" stroke="#fff" stroke-width="1.5" fill="none"/></svg>
          www.pavrel.com
        </li>
      </ul>
    </div>
  </section>
</body>
</html>
```